Graphic Design for 2026 AGGMS Summit – 4:3 Ratio Event Image

The Allied Guild of Garment Makers and Suppliers (AGGMS) is seeking a high-quality, professional graphic to serve as the primary visual template for our 2026 AGGMS Summit & Showcase. This image will be used across digital, print, and on-site event materials. We need a visually striking, industry-relevant design that reflects the uniform, image apparel, and workwear industry and captures the spirit of innovation, networking, and global connection that defines our annual convention.

Key Details:
Event Name: 2026 AGGMS Summit & Showcase

Audience: Uniform manufacturers, distributors, and suppliers serving public safety, hospitality, healthcare, corporate, and industrial markets.

Purpose of Image:

Serve as the main branding graphic for the convention.

Be adaptable for use on our website, social media, email campaigns, signage, and printed materials.

Provide a modern, professional, future-focused look appealing to business decision-makers in the uniform and workwear sector.

Design Requirements:
Format: Layered file delivery (Adobe Illustrator or Photoshop).

If Photoshop, final file must be minimum 2500px wide for high-quality print output.

Aspect Ratio: 4:3 (landscape).

Style:

Clean, professional, and corporate.

Forward-looking, innovative feel (not dated or generic).

Should represent the diverse industries where uniforms are worn (public safety, healthcare, hospitality, industrial, corporate office).

Abstract or conceptual elements (e.g., flowing fabric, silhouettes of professionals, global connections) are welcome. Avoid clip-art or overly literal graphics.

Color Palette: Prefer use of AGGMS’s primary brand colors where possible:

Blue: #204295

Red: #EC1F25
Designers may incorporate complementary colors to enhance the look, but these two should be prominent.

Deliverables:
Main design file in Illustrator (.AI) or Photoshop (.PSD), layered and editable.

High-resolution exported version for immediate use.

Adaptable design suitable for other sizes and formats in future.

Inspiration:
We want a bold, memorable image that conveys:

The professionalism and scale of the uniform industry.

Innovation, progress, and networking.

Global reach and cross-industry connections fostered by AGGMS’s annual convention.

Usage Rights:
AGGMS will retain full rights to the final chosen design for unlimited future use across digital and print channels.

Attached is a rough concept I created. I’m not satisfied with it, but it shows the basic layout idea. I’d like you to take the concept to a much more professional, polished level, incorporating our brand colors (Blue #204295, Red #EC1F25) and a modern, corporate feel.

Requirements
Must have
• Include this text: Threads of Tomorrow: The Weave of Vision, Talent, and Promise AGGMS 2026 SUMMIT Uniform and Workwear Professionals

```html
<!DOCTYPE html>
<html lang="en">
<head>
<meta charset="utf-8">
<title>AGGMS 2026 Summit – Uniform and Workwear Professionals</title>
<link rel="stylesheet" href="https://fonts.googleapis.com/css2?family=Roboto+Condensed:wght@800&family=Caveat:wght@500&family=Josefin+Sans:wght@300;700&display=swap">
<style>
  :root {
    --brand-blue: #0a2fa3;
    --brand-blue-deep: #062482;
    --brand-red: #ec2526;
    --ink: #0b0b0b;
    --ink-soft: #2a2a2a;
    --paper: #ffffff;
    --garment-navy: #1c2a45;
    --garment-red: #d8302c;
    --garment-sky: #4f86d6;
    --garment-crimson: #b51f32;
    --garment-maroon: #7a2046;
  }
  * { margin: 0; padding: 0; box-sizing: border-box; }
  html, body { width: 1200px; height: 900px; overflow: hidden; background: var(--paper); }
  .poster { position: relative; width: 1200px; height: 900px; overflow: hidden; }

  .hero-band {
    position: absolute; left: 0; top: 0; width: 1200px; height: 515px;
    background: var(--brand-blue);
  }
  .globe-backdrop {
    position: absolute; left: 0; top: 0; width: 560px; height: 515px;
    background: radial-gradient(ellipse at 30% 55%, rgba(90,130,230,0.45) 0%, rgba(10,47,163,0) 65%);
  }
  .hero-title {
    position: absolute; left: 0; top: 48px; width: 1200px;
    font-family: "Roboto Condensed", "Arial Narrow", sans-serif;
    font-weight: 800; font-size: 104px; line-height: 90px;
    color: var(--paper); text-align: center; text-transform: uppercase;
    letter-spacing: -0.5px;
    text-shadow: 0 0 6px var(--brand-blue-deep), 0 2px 4px var(--brand-blue-deep);
  }
  .garment-lineup {
    position: absolute; left: 111px; top: 262px; width: 980px; height: 253px;
    background: linear-gradient(90deg,
      var(--garment-navy) 0%, var(--garment-navy) 17%,
      var(--garment-red) 23%, var(--garment-red) 36%,
      var(--garment-sky) 42%, var(--garment-sky) 56%,
      var(--garment-crimson) 63%, var(--garment-crimson) 74%,
      var(--garment-maroon) 82%, var(--garment-maroon) 100%);
    border-radius: 60px 60px 0 0;
  }

  .theme-band {
    position: absolute; left: 0; top: 515px; width: 1200px; height: 164px;
    background: var(--paper);
  }
  .theme-title {
    position: absolute; left: 0; top: 6px; width: 1200px; text-align: center;
    font-family: "Caveat", cursive; font-weight: 500; font-size: 112px; line-height: 110px;
    color: var(--brand-red);
  }
  .theme-subtitle {
    position: absolute; left: 0; top: 106px; width: 1200px; text-align: center;
    font-family: "Josefin Sans", sans-serif; font-weight: 300; font-size: 34px;
    letter-spacing: 0.2em; color: var(--ink-soft); text-transform: uppercase;
  }

  .info-band {
    position: absolute; left: 0; top: 679px; width: 1200px; height: 221px;
    background: var(--brand-red);
    font-family: "Josefin Sans", sans-serif; font-weight: 700;
  }
  .event-name {
    position: absolute; left: 76px; top: 54px;
    font-size: 54px; line-height: 58px; color: var(--ink); text-transform: uppercase;
  }
  .event-name .year { color: var(--paper); margin-left: 18px; }
  .divider {
    position: absolute; top: 56px; width: 4px; height: 104px; background: var(--paper);
  }
  .divider--first { left: 503px; }
  .divider--second { left: 762px; }

  .event-date { position: absolute; left: 552px; top: 56px; width: 180px; height: 104px; }
  .event-date .month {
    position: absolute; left: -18px; top: 34px; width: 104px;
    transform: rotate(-90deg); transform-origin: center;
    font-size: 40px; line-height: 36px; color: var(--paper); text-align: center;
  }
  .event-date .days {
    position: absolute; left: 44px; top: 0; font-size: 76px; line-height: 64px; color: var(--ink);
  }
  .event-date .date-year {
    position: absolute; left: 46px; top: 64px; font-size: 48px; line-height: 44px; color: var(--ink);
  }

  .venue-pin { position: absolute; left: 794px; top: 53px; width: 76px; height: 108px; }
  .venue {
    position: absolute; left: 891px; top: 63px;
    font-size: 29px; line-height: 37px; color: var(--paper); text-transform: uppercase;
  }
</style>
</head>
<body>
<main class="poster">
  <section class="hero-band">
    <div class="globe-backdrop" role="img" aria-label="Faint dotted world globe with connection lines"></div>
    <h1 class="hero-title">Uniform &amp; Workwear<br>Professionals</h1>
    <div class="garment-lineup" role="img" aria-label="Row of uniforms: police shirt, firefighter jacket, medical scrubs, hospitality blazer and server apron"></div>
  </section>

  <section class="theme-band">
    <p class="theme-title">Threads Of Tomorrow</p>
    <p class="theme-subtitle">The Weave of Vision, Talent, and Promise</p>
  </section>

  <section class="info-band">
    <p class="event-name">AGGMS<span class="year">2026</span><br>Summit</p>
    <span class="divider divider--first"></span>
    <div class="event-date">
      <span class="month">May</span>
      <span class="days">3-5</span>
      <span class="date-year">2026</span>
    </div>
    <span class="divider divider--second"></span>
    <svg class="venue-pin" viewBox="0 0 76 108" aria-hidden="true">
      <path d="M38 6 C20 6 7 19 7 37 C7 58 38 88 38 88 C38 88 69 58 69 37 C69 19 56 6 38 6 Z" fill="none" stroke="#fff" stroke-width="6" stroke-linejoin="round"/>
      <circle cx="38" cy="37" r="10" fill="none" stroke="#fff" stroke-width="6"/>
      <path d="M18 92 C8 95 10 103 38 103 C66 103 68 95 58 92" fill="none" stroke="#fff" stroke-width="5" stroke-linecap="round"/>
    </svg>
    <p class="venue">Harborview<br>Grand Plaza<br>Boston, MA, USA</p>
  </section>
</main>
</body>
</html>
```